Walk Beside The River

Business Card design

Target Market(s)

People who require support in the commnity

Industry/Entity Type

Mental Health Support

Contact Information for Business Card

Mental Health Support Rosalind Tavener walkbesidetheriver@mailcove.com.au 0481 637 092 PO Box 926 Corranvale QLD 4571

Colors
6B429C
8869AF
B7A5CE
E3DAEB
F3F0F8

Requirements
Must have
• Logo & details listed above
Should not have
• No red or orange

```html
<!DOCTYPE html>
<html lang="en">
<head>
<meta charset="utf-8">
<title>Walk Beside The River – Business Card</title>
<link rel="stylesheet" href="https://fonts.googleapis.com/css2?family=Open+Sans:wght@400;600;700;800&display=swap">
<style>
  :root {
    --stage: #222222;
    --card-dark: #1d1c22;
    --card-light: #ffffff;
    --edge-yellow: #ece72c;
    --band-yellow: #f0e930;
    --purple: #6b429c;
    --ink: #111111;
    --dark-mark: #2c2b33;
  }
  * { box-sizing: border-box; margin: 0; padding: 0; }
  html, body {
    width: 1200px; height: 780px; overflow: hidden;
    background: var(--stage);
    font-family: "Open Sans", Arial, sans-serif;
  }
  .canvas {
    width: 1200px; height: 780px;
    display: flex; align-items: center; justify-content: center; gap: 40px;
  }

  .card {
    position: relative;
    width: 540px; height: 309px;
    border-radius: 20px;
    overflow: hidden;
    flex: none;
    box-shadow: 0 0 0 3px var(--edge-yellow), 0 18px 40px rgba(0,0,0,.55);
  }

  /* Back */
  .card-back {
    background: var(--card-dark);
    display: flex; align-items: center; justify-content: center;
  }
  .back-name {
    color: var(--dark-mark);
    font-weight: 800;
    font-size: 32px;
  }

  /* Front */
  .card-front { background: var(--card-light); }

  .brand {
    position: absolute; right: 26px; top: 34px;
    display: flex; align-items: center; gap: 10px;
  }
  .brand-dot {
    width: 40px; height: 40px; border-radius: 50%;
    background: var(--purple);
    flex: none;
  }
  .brand-name {
    color: var(--purple);
    font-weight: 700;
    font-size: 18px;
    white-space: nowrap;
  }

  .name-flag {
    position: absolute; left: 0; top: 114px;
    width: 24px; height: 50px;
    background: var(--band-yellow);
  }
  .person { position: absolute; left: 34px; top: 110px; }
  .person-name {
    color: var(--purple);
    font-weight: 700;
    font-size: 28px;
    line-height: 1.1;
    white-space: nowrap;
  }
  .person-role {
    color: var(--ink);
    font-weight: 600;
    font-size: 14px;
    margin-top: 2px;
  }

  .contacts {
    position: absolute; left: 96px; top: 186px;
    list-style: none;
    color: var(--ink);
    font-size: 13px;
    line-height: 1.4;
  }
  .contacts li { display: flex; align-items: center; gap: 8px; white-space: nowrap; }
  .contacts svg { width: 13px; height: 13px; fill: var(--purple); flex: none; }

  .tagline-band {
    position: absolute; left: 0; right: 0; top: 252px;
    height: 32px;
    background: var(--band-yellow);
    display: flex; align-items: center; justify-content: center;
    padding-left: 80px;
    color: var(--ink);
    font-size: 13px;
    font-weight: 600;
    white-space: nowrap;
  }
</style>
</head>
<body>
<main class="canvas">

  <section class="card card-back" aria-label="Business card, back">
    <p class="back-name">Walk Beside The River</p>
  </section>

  <section class="card card-front" aria-label="Business card, front">
    <div class="brand">
      <span class="brand-dot"></span>
      <span class="brand-name">Walk Beside The River</span>
    </div>

    <span class="name-flag"></span>
    <div class="person">
      <h1 class="person-name">Halina Vorbeck</h1>
      <p class="person-role">CEO/Director</p>
    </div>

    <ul class="contacts">
      <li>
        <svg viewBox="0 0 24 24" aria-hidden="true"><path d="M6.6 10.8a15.2 15.2 0 0 0 6.6 6.6l2.2-2.2a1 1 0 0 1 1-.25 11.4 11.4 0 0 0 3.6.57 1 1 0 0 1 1 1V20a1 1 0 0 1-1 1A17 17 0 0 1 3 4a1 1 0 0 1 1-1h3.5a1 1 0 0 1 1 1c0 1.25.2 2.45.57 3.6a1 1 0 0 1-.25 1z"/></svg>
        0481 637 092
      </li>
      <li>
        <svg viewBox="0 0 24 24" aria-hidden="true"><path d="M3 5h18a1 1 0 0 1 1 1v12a1 1 0 0 1-1 1H3a1 1 0 0 1-1-1V6a1 1 0 0 1 1-1zm9 7.2L4 7.3V8l8 5 8-5v-.7z"/></svg>
        walkbesidetheriver@mailcove.com.au
      </li>
      <li>
        <svg viewBox="0 0 24 24" aria-hidden="true"><path d="M12 2a7 7 0 0 0-7 7c0 5 7 13 7 13s7-8 7-13a7 7 0 0 0-7-7zm0 9.5A2.5 2.5 0 1 1 12 6.5a2.5 2.5 0 0 1 0 5z"/></svg>
        PO Box 926 Corranvale QLD 4571
      </li>
    </ul>

    <div class="tagline-band">Mental Health Support Rosalind Tavener</div>
  </section>

</main>
</body>
</html>
```